Business Card for brovaLINK

Create a Business Card with an existing logo for brovaLINK AG. We are a Information Technology company that does consulting and developing SW to automate business processes. The main colors are given from the logo.

Industry/Entity Type

Business

Requirements
Nice to have
• we use a a font style Century Gothic in our documents

```html
<!DOCTYPE html>
<html lang="en">
<head>
<meta charset="utf-8">
<title>brovaLINK AG – Business Card</title>
<link href="https://fonts.googleapis.com/css2?family=Didact+Gothic&family=Oswald:wght@500&display=swap" rel="stylesheet">
<style>
  :root {
    --stage: #e9e7e3;
    --card: #ffffff;
    --ink: #2b2b2b;
    --band: #1c1c1c;
    --band-text: #f2f2f2;
    --muted: #bdbdbd;
    --green: #8cc63f;
    --green-deep: #5aa321;
    --blue: #1f4e8c;
  }
  * { box-sizing: border-box; margin: 0; padding: 0; }
  html, body { width: 1200px; height: 970px; overflow: hidden; }
  body {
    background: var(--stage);
    font-family: "Didact Gothic", "Century Gothic", sans-serif;
    color: var(--ink);
    position: relative;
  }
  .card {
    position: absolute;
    left: 220px;
    width: 760px;
    height: 434px;
    background: var(--card);
    overflow: hidden;
    box-shadow: 0 10px 28px rgba(0,0,0,.18);
  }
  .card--front { top: 40px; }
  .card--back { top: 496px; }

  .swoosh { position: absolute; left: 0; bottom: 0; width: 760px; height: 434px; }

  .brand {
    position: absolute;
    color: var(--ink);
    text-transform: uppercase;
    line-height: 1;
    white-space: nowrap;
  }
  .card--front .brand {
    left: 0; right: 0; top: 150px;
    text-align: center;
    font-size: 56px;
    letter-spacing: 6px;
  }
  .card--back .brand {
    left: 40px; top: 158px;
    font-size: 32px;
    letter-spacing: 3px;
  }

  .info-band {
    position: absolute;
    left: 360px;
    top: 30px;
    width: 400px;
    height: 300px;
    background: var(--band);
    color: var(--band-text);
    padding: 66px 34px 0 40px;
  }
  .person__name {
    font-family: "Oswald", sans-serif;
    font-weight: 500;
    font-size: 30px;
    letter-spacing: 1.5px;
    text-transform: uppercase;
  }
  .person__role {
    font-size: 13px;
    letter-spacing: 2px;
    text-transform: uppercase;
    color: var(--muted);
    margin-bottom: 30px;
  }
  .contacts { list-style: none; display: grid; grid-template-columns: 1fr 1fr; gap: 16px 18px; }
  .contacts li { display: flex; align-items: center; gap: 9px; font-size: 14px; white-space: nowrap; }
  .contacts svg { width: 20px; height: 20px; flex: none; }

  .address {
    position: absolute;
    left: 360px;
    top: 352px;
    font-size: 18px;
    letter-spacing: 1px;
    color: var(--ink);
  }
  .edge-line {
    position: absolute;
    left: 0; bottom: 0;
    width: 100%;
    height: 8px;
    background: var(--blue);
  }
</style>
</head>
<body>

<section class="card card--front" aria-label="Card front">
  <svg class="swoosh" viewBox="0 0 760 434" aria-hidden="true">
    <path d="M0 434 L0 372 C220 404 500 404 760 300 L760 318 C520 420 240 434 0 434 Z" fill="var(--green)"/>
    <path d="M0 434 C260 430 520 410 760 318 L760 434 Z" fill="var(--green-deep)"/>
  </svg>
  <p class="brand">brovaLINK</p>
</section>

<section class="card card--back" aria-label="Card back">
  <p class="brand">brovaLINK</p>

  <div class="info-band">
    <h1 class="person__name">Lena Hoffer</h1>
    <p class="person__role">General Manager</p>
    <ul class="contacts">
      <li>
        <svg viewBox="0 0 20 20" aria-hidden="true"><circle cx="10" cy="10" r="9" fill="none" stroke="currentColor" stroke-width="1.4"/><path d="M7 5.5l2 2-1 1.2c.6 1.3 1.5 2.2 2.8 2.8l1.2-1 2 2-1.2 1.5C9.5 14 6 10.5 5.5 7.2Z" fill="currentColor"/></svg>
        041 728 5530
      </li>
      <li>
        <svg viewBox="0 0 20 20" aria-hidden="true"><circle cx="10" cy="10" r="9" fill="none" stroke="currentColor" stroke-width="1.4"/><rect x="5.5" y="6.5" width="9" height="7" rx="1" fill="none" stroke="currentColor" stroke-width="1.3"/><path d="M5.8 7l4.2 3.3L14.2 7" fill="none" stroke="currentColor" stroke-width="1.3"/></svg>
        lena@brovalink.ch
      </li>
      <li>
        <svg viewBox="0 0 20 20" aria-hidden="true"><circle cx="10" cy="10" r="9" fill="none" stroke="currentColor" stroke-width="1.4"/><rect x="7" y="5" width="6" height="10" rx="1" fill="none" stroke="currentColor" stroke-width="1.3"/><circle cx="10" cy="13" r=".8" fill="currentColor"/></svg>
        041 728 5531
      </li>
      <li>
        <svg viewBox="0 0 20 20" aria-hidden="true"><circle cx="10" cy="10" r="9" fill="none" stroke="currentColor" stroke-width="1.4"/><circle cx="10" cy="10" r="5" fill="none" stroke="currentColor" stroke-width="1.2"/><path d="M5 10h10M10 5c-2 3-2 7 0 10M10 5c2 3 2 7 0 10" fill="none" stroke="currentColor" stroke-width="1"/></svg>
        www.brovalink.ch
      </li>
    </ul>
  </div>

  <p class="address">24 Seefeld Road, 2nd floor, Zug</p>
  <div class="edge-line"></div>
</section>

</body>
</html>
```